Spring Detox sale graphics for social media

You MUST read the Brief in the WORD document and follow the instructions there. I want to create 10 social media graphics (new Instagram size 4:5 (1080 x 1350 pixels) focusing on our Mother’s Day Spring Detox Sale graphics, using any of the pics attached. Use the attached pics, NO RANDOM STOCK PHOTOGRAPHY. For the color scheme of the graphics, they should all be complementary to the product colors or feel like Spring time.

Target Market(s)

primarily women

Requirements
Must have
• the photos and text attached

```html
<!DOCTYPE html>
<html lang="en">
<head>
<meta charset="utf-8">
<title>Mother's Day Spring Detox Sale – Social Set</title>
<link href="https://fonts.googleapis.com/css2?family=Bebas+Neue&family=Montserrat:wght@400;500;600&family=Playfair+Display:wght@700;900&family=Great+Vibes&display=swap" rel="stylesheet">
<style>
  :root{
    --board:#9a9a9a;
    --blush:#fbe3ea;
    --rose:#e2538c;
    --ink:#2e2a2c;
    --lilac-paper:#efe7f0;
    --violet:#8c67b1;
    --violet-band:#9270b4;
    --magenta:#c4469b;
    --sage-paper:#e6e9e1;
    --forest:#2f5a45;
    --leaf:#4d8a3b;
    --pink-ribbon:#e55d8b;
    --pink-num:#ea74a8;
    --pink-text:#d9508f;
    --white:#ffffff;
  }
  *{margin:0;padding:0;box-sizing:border-box}
  html,body{width:957px;height:1200px;overflow:hidden;background:var(--board)}
  .board{position:relative;width:957px;height:1200px}
  .post{position:absolute;width:454px;height:568px;overflow:hidden}
  .abs{position:absolute}
  .center{left:0;right:0;text-align:center}

  /* Post 1 */
  .post--portrait{left:16px;top:17px;background:var(--blush)}
  .portrait-photo{left:0;top:0;width:454px;height:300px;
    background:linear-gradient(180deg,#7a4a35 0%,#a77a63 45%,#d9b3ad 75%,var(--blush) 100%)}
  .big-condensed{font-family:"Bebas Neue",sans-serif;color:var(--rose);font-size:78px;line-height:1;top:242px}
  .sale-title{font-family:"Montserrat",sans-serif;font-weight:400;color:var(--ink);font-size:27px;top:314px;letter-spacing:.5px}
  .script-line{top:352px;display:flex;align-items:center;justify-content:center;gap:8px}
  .script-line .rule{width:46px;height:1.5px;background:var(--rose)}
  .script{font-family:"Great Vibes",cursive;color:var(--rose);font-size:30px;line-height:1}
  .bottles-row-1{left:66px;top:404px;width:334px;height:150px}

  .bottle-shot{border-radius:10px;background:linear-gradient(180deg,#f7f7f8 0%,#e9e6ea 55%,#d9c3d6 100%)}

  /* Ribbon posts */
  .post--lilac{left:485px;top:18px;background:var(--lilac-paper)}
  .post--pink{left:485px;top:611px;background:#f1e7ee}
  .ribbon{left:96px;width:262px;height:36px;color:var(--white);font-family:"Playfair Display",serif;font-weight:700;font-size:16px;
    display:flex;align-items:center;justify-content:center;letter-spacing:.5px;
    clip-path:polygon(0 0,100% 0,96% 50%,100% 100%,0 100%,4% 50%)}
  .ribbon--violet{top:29px;background:var(--violet)}
  .ribbon--pink{top:51px;background:var(--pink-ribbon)}
  .serif-num{font-family:"Playfair Display",serif;font-weight:900;line-height:1}
  .num-pct{font-size:102px}
  .num-off{font-size:64px}
  .serif-caps{font-family:"Playfair Display",serif;font-weight:700;font-size:14.5px;letter-spacing:.3px}
  .flower{border-radius:50%;background:radial-gradient(circle,#f4b8cf 0%,#f0cfe0 50%,rgba(240,207,224,0) 72%)}
  .flower--coral{background:radial-gradient(circle,#f3877f 0%,#f6b9b4 45%,rgba(246,185,180,0) 72%)}
  .bottles-stack{left:95px;top:366px;width:266px;height:156px}

  .footer-band{left:0;bottom:0;width:454px;height:31px;background:var(--violet-band);display:flex;align-items:center;justify-content:space-between;padding:0 26px;
    color:var(--white);font-family:"Montserrat",sans-serif;font-size:10px;letter-spacing:.3px}
  .footer-band span{display:flex;align-items:center;gap:5px}
  .footer-line{left:0;bottom:0;width:454px;height:29px;background:#ece1ea;color:var(--pink-text);font-family:"Montserrat",sans-serif;font-size:9.5px;
    display:flex;align-items:center;justify-content:center;letter-spacing:.3px}

  /* Post 3 */
  .post--sage{left:16px;top:602px;height:567px;background:var(--sage-paper)}
  .product-photo{left:0;top:0;width:454px;height:208px;background:linear-gradient(180deg,#e4e4e6 0%,#f0eff0 60%,#dcdcde 100%)}
  .photo-gap{left:0;top:208px;width:454px;height:4px;background:var(--white)}
  .sage-title{font-family:"Montserrat",sans-serif;font-weight:500;color:var(--forest);font-size:33px;top:244px;letter-spacing:.3px}
  .sage-offer{font-family:"Montserrat",sans-serif;font-weight:600;color:var(--leaf);font-size:55px;top:290px;line-height:1.1}
  .sage-sub{font-family:"Montserrat",sans-serif;font-weight:600;color:var(--forest);font-size:25px;top:364px}
  .sage-rule{left:20px;top:418px;width:409px;height:1px;background:#c9cec2}
  .benefit{top:447px;width:120px;text-align:center;font-family:"Montserrat",sans-serif;color:var(--forest)}
  .benefit svg{display:block;margin:0 auto 10px}
  .benefit b{display:block;font-weight:600;font-size:12px;letter-spacing:.4px}
  .benefit small{display:block;font-size:8.5px;margin-top:5px;letter-spacing:.3px}
</style>
</head>
<body>
<main class="board">

  <!-- Post 1: portrait -->
  <section class="post post--portrait">
    <div class="abs portrait-photo" role="img" aria-label="Smiling woman in a white sweater in a kitchen"></div>
    <div class="abs center big-condensed">25% OFF</div>
    <div class="abs center sale-title">MOTHER’S DAY SALE</div>
    <div class="abs center script-line"><i class="rule"></i><span class="script">Feel Amazing Again!</span><i class="rule"></i></div>
    <div class="abs bottles-row-1 bottle-shot" role="img" aria-label="Four supplement bottles in a row"></div>
  </section>

  <!-- Post 2: lilac floral -->
  <section class="post post--lilac">
    <div class="abs flower" style="left:-20px;top:90px;width:150px;height:140px" role="img" aria-label="Cherry blossom branch"></div>
    <div class="abs flower" style="left:-10px;top:270px;width:130px;height:150px" role="img" aria-label="Cherry blossom branch"></div>
    <div class="abs flower" style="left:335px;top:150px;width:140px;height:130px" role="img" aria-label="Cherry blossom branch"></div>
    <div class="abs flower" style="left:345px;top:320px;width:120px;height:160px" role="img" aria-label="Cherry blossom branch"></div>
    <div class="abs ribbon ribbon--violet">MOTHER’S DAY</div>
    <div class="abs center serif-num num-pct" style="top:86px;color:var(--violet)">25%</div>
    <div class="abs center serif-num num-off" style="top:180px;color:var(--violet)">OFF</div>
    <div class="abs center serif-caps" style="top:252px;color:var(--violet)">SPRING DETOX SALE</div>
    <div class="abs center script" style="top:282px;font-size:31px;color:var(--magenta);line-height:1.08">Spring Cleanse,<br>Summer Glow</div>
    <div class="abs bottles-stack bottle-shot" role="img" aria-label="Four supplement bottles grouped together"></div>
    <div class="abs footer-band">
      <span><svg width="14" height="14" viewBox="0 0 14 14" fill="none" stroke="#fff" stroke-width="1"><circle cx="7" cy="7" r="6"/><path d="M5 4h4M6 4v3l-2 3h6L8 7V4"/></svg>DETOX.</span>
      <span><svg width="16" height="12" viewBox="0 0 16 12" fill="none" stroke="#fff" stroke-width="1"><path d="M8 2c2 2 2 6 0 8-2-2-2-6 0-8zM8 10C5 10 2 8 1 5c3 0 5 2 7 5zM8 10c3 0 6-2 7-5-3 0-5 2-7 5z"/></svg>REBALANCE.</span>
      <span><svg width="14" height="14" viewBox="0 0 14 14" fill="none" stroke="#fff" stroke-width="1"><circle cx="7" cy="7" r="2.5"/><circle cx="7" cy="7" r="6"/></svg>REJUVENATE.</span>
    </div>
  </section>

  <!-- Post 3: sage -->
  <section class="post post--sage">
    <div class="abs product-photo" role="img" aria-label="Four supplement bottles on a white shelf"></div>
    <div class="abs photo-gap"></div>
    <div class="abs center sage-title">SPRING DETOX SALE</div>
    <div class="abs center sage-offer">25% OFF</div>
    <div class="abs center sage-sub">ALL SUPPLEMENTS</div>
    <svg class="abs" style="left:37px;top:332px" width="52" height="50" viewBox="0 0 52 50" fill="var(--leaf)">
      <path d="M18 14l3 10 10 3-10 3-3 10-3-10-10-3 10-3z"/><path d="M32 0l2 6 6 2-6 2-2 6-2-6-6-2 6-2z"/><path d="M38 30l1.5 4.5 4.5 1.5-4.5 1.5L38 42l-1.5-4.5L32 36l4.5-1.5z"/>
    </svg>
    <svg class="abs" style="left:358px;top:330px" width="52" height="50" viewBox="0 0 52 50" fill="var(--leaf)">
      <path d="M18 14l3 10 10 3-10 3-3 10-3-10-10-3 10-3z"/><path d="M34 0l2 6 6 2-6 2-2 6-2-6-6-2 6-2z"/><path d="M42 30l1.5 4.5 4.5 1.5-4.5 1.5L42 42l-1.5-4.5L36 36l4.5-1.5z"/>
    </svg>
    <div class="abs sage-rule"></div>
    <div class="abs benefit" style="left:20px">
      <svg width="50" height="50" viewBox="0 0 50 50" fill="none" stroke="var(--leaf)" stroke-width="1.3"><circle cx="25" cy="25" r="23.5"/><path d="M25 15c4 6 6 9 6 12a6 6 0 0 1-12 0c0-3 2-6 6-12z"/><path d="M14 24c2 8 6 11 11 11s9-3 11-11"/></svg>
      <b>CLEANSE</b><small>YOUR BODY</small>
    </div>
    <div class="abs benefit" style="left:165px">
      <svg width="50" height="50" viewBox="0 0 50 50" fill="none" stroke="var(--leaf)" stroke-width="1.3"><circle cx="25" cy="25" r="23.5"/><circle cx="25" cy="14" r="3"/><path d="M20 20h10v10h-2v10h-6V30h-2z"/><path d="M15 16v-3h3M35 16v-3h-3M15 34v3h3M35 34v3h-3"/></svg>
      <b>BALANCE</b><small>YOUR HORMONES</small>
    </div>
    <div class="abs benefit" style="left:311px">
      <svg width="50" height="50" viewBox="0 0 50 50" fill="none" stroke="var(--leaf)" stroke-width="1.3"><circle cx="25" cy="25" r="23.5"/><path d="M27 13l-7 13h6l-3 11 8-14h-6z"/><path d="M14 25h3M33 25h3M17 16l2 2M33 16l-2 2M17 34l2-2M33 34l-2-2"/></svg>
      <b>BOOST</b><small>YOUR ENERGY</small>
    </div>
  </section>

  <!-- Post 4: pink floral -->
  <section class="post post--pink">
    <div class="abs flower flower--coral" style="left:20px;top:180px;width:110px;height:130px" role="img" aria-label="Pink wildflowers"></div>
    <div class="abs flower flower--coral" style="left:340px;top:170px;width:110px;height:140px" role="img" aria-label="Pink wildflowers"></div>
    <div class="abs flower flower--coral" style="left:15px;top:360px;width:100px;height:120px" role="img" aria-label="Pink wildflowers"></div>
    <div class="abs flower flower--coral" style="left:370px;top:370px;width:90px;height:130px" role="img" aria-label="Pink wildflowers"></div>
    <svg class="abs" style="left:215px;top:18px" width="22" height="20" viewBox="0 0 22 20"><path d="M11 19C4 13 0 10 0 5.5A5 5 0 0 1 11 3a5 5 0 0 1 11 2.5C22 10 18 13 11 19z" fill="var(--pink-ribbon)"/></svg>
    <div class="abs ribbon ribbon--pink">MOTHER’S DAY</div>
    <div class="abs center serif-num num-pct" style="top:108px;color:var(--pink-num)">25%</div>
    <div class="abs center serif-num num-off" style="top:204px;color:var(--pink-num)">OFF</div>
    <svg class="abs" style="left:136px;top:262px" width="16" height="14" viewBox="0 0 22 20"><path d="M11 19C4 13 0 10 0 5.5A5 5 0 0 1 11 3a5 5 0 0 1 11 2.5C22 10 18 13 11 19z" fill="var(--pink-ribbon)"/></svg>
    <div class="abs center serif-caps" style="top:275px;color:var(--pink-text)">SPRING DETOX SALE</div>
    <div class="abs center script" style="top:302px;font-size:40px;color:var(--pink-text)">Everything!</div>
    <div class="abs bottles-stack bottle-shot" role="img" aria-label="Four supplement bottles grouped together"></div>
    <div class="abs footer-line">DETOX - REBALANCE - REJUVENATE</div>
  </section>

</main>
</body>
</html>
```